Quillbrookes websites redesign

Www.quill-brookes.com needs to be redesigned along with updations. The incremental material will be provided for the updations. We are looking for complete redesign of the pages with the new content. The complete write up will be provided soon

Target Market(s)

Global

Coding

Coded - Design and coding required

Number of Pages Required

5+ page

Requirements
Must have
• A clean and slick design for the Consulting.
Should not have
• Too many pictures which reduces the speed of the site

```html
<!DOCTYPE html>
<html lang="en">
<head>
<meta charset="utf-8">
<title>Quillbrookes – Consultancy</title>
<link rel="stylesheet" href="https://fonts.googleapis.com/css2?family=Roboto+Condensed:wght@400;700&family=Raleway:wght@400;500&family=Open+Sans:wght@400;600;700&display=swap">
<style>
:root{
  --blue:#0b8ad6;
  --blue-btn:#1a8fdc;
  --navy:#1e2a44;
  --maroon:#3a1a1f;
  --grey-bg:#ebebeb;
  --text:#555b63;
  --white:#fff;
}
*{margin:0;padding:0;box-sizing:border-box}
html,body{width:1200px;height:2590px;overflow:hidden;background:var(--white)}
body{position:relative;font-family:"Open Sans",sans-serif;color:var(--text)}
.abs{position:absolute}
.topline{left:0;top:0;width:1200px;height:7px;background:var(--blue)}
.site-header{left:0;top:7px;width:1200px;height:105px;background:var(--white)}
.brand{display:flex;align-items:center;gap:12px;font-family:"Open Sans",sans-serif;font-weight:600;font-size:36px;color:var(--navy)}
.brand-dot{width:42px;height:42px;border-radius:50%;background:var(--blue)}
.site-header .brand{left:78px;top:30px}
.main-nav{left:394px;top:28px;display:flex;font-family:"Roboto Condensed",sans-serif;font-size:19px;color:#333;text-transform:uppercase}
.main-nav a{display:block;height:46px;line-height:46px;padding:0 21px;color:inherit;text-decoration:none;margin-right:0}
.main-nav a.active{background:var(--navy);color:var(--white);margin-right:-8px}
.hero{left:0;top:112px;width:1200px;height:625px}
.hero-title{left:78px;top:140px;font-family:"Roboto Condensed",sans-serif;font-size:46px;line-height:62px;color:var(--white)}
.btn{display:block;text-align:center;text-decoration:none;font-family:"Roboto Condensed",sans-serif;text-transform:uppercase}
.btn-contact{left:78px;top:352px;width:193px;height:61px;line-height:61px;background:var(--blue-btn);color:var(--white);font-family:"Open Sans",sans-serif;font-weight:600;font-size:22px;letter-spacing:.5px}
.welcome-title{left:0;top:785px;width:1200px;text-align:center;font-family:"Raleway",sans-serif;font-size:46px;color:var(--maroon)}
.welcome-title span{color:var(--blue)}
.welcome-text{left:160px;top:870px;width:880px;text-align:center;font-size:15.5px;line-height:25px}
.btn-more{left:521px;top:972px;width:156px;height:47px;line-height:47px;background:var(--navy);color:var(--white);font-size:19px}
.consultancy{left:0;top:1081px;width:1200px;height:675px;background:var(--grey-bg);border-top:1px solid #d6d6d6}
.section-title{left:0;width:1200px;text-align:center;font-family:"Raleway",sans-serif;font-size:41px;color:var(--blue)}
.section-lead{left:200px;width:800px;text-align:center;font-size:15px;line-height:26px}
.card{top:1352px;width:499px;height:312px;color:var(--white);text-align:center}
.card-dark{left:78px;background:var(--navy)}
.card-blue{left:623px;background:var(--blue)}
.card-icon{position:absolute;left:181px;top:-69px;width:138px;height:138px;border-radius:50%;background:var(--white);display:flex;align-items:center;justify-content:center}
.card-dark .card-icon{border:4px solid var(--navy)}
.card-blue .card-icon{border:4px solid var(--blue)}
.card h3{position:absolute;left:0;top:92px;width:100%;font-family:"Roboto Condensed",sans-serif;font-weight:400;font-size:25px;letter-spacing:.3px}
.card .rule{position:absolute;left:202px;top:134px;width:95px;height:2px;background:var(--white)}
.card p{position:absolute;left:18px;top:168px;width:463px;font-size:15.5px;line-height:25px}
.case-study{left:0;top:1756px;width:1200px;height:470px}
.case-title{left:0;top:1805px;width:1200px;text-align:center;font-family:"Raleway",sans-serif;font-size:50px;color:var(--white)}
.case-lead{left:180px;top:1879px;width:840px;text-align:center;font-size:15.5px;line-height:26px;color:var(--white)}
.case-facts{left:0;top:1950px;width:1200px;text-align:center;font-size:21px;line-height:31px;color:var(--white)}
.case-facts b{font-weight:700}
.slide-arrow{top:1930px;width:62px;height:62px}
.case-banner{left:226px;top:2093px;width:748px;height:57px;line-height:57px;background:var(--blue-btn);color:var(--white);text-align:center;font-weight:700;font-size:21px}
.site-footer{left:0;top:2226px;width:1200px;height:290px;background:var(--blue);color:var(--white)}
.footer-col{top:2258px}
.footer-col h4{font-family:"Roboto Condensed",sans-serif;font-weight:400;font-size:26px;margin-bottom:12px}
.footer-col p,.footer-col li{font-size:15.5px;line-height:25px}
.footer-col ul{list-style:none}
.footer-col li{line-height:31px}
.footer-col li::before{content:"";display:inline-block;width:8px;height:8px;border-right:3px solid var(--white);border-top:3px solid var(--white);transform:rotate(45deg);margin:0 12px 2px 0}
.footer-brand{font-size:32px;color:var(--white)}
.footer-brand .brand-dot{background:var(--white);width:36px;height:36px}
.news-input{width:236px;height:36px;border:1.5px solid var(--white);padding:0 12px;line-height:33px;font-size:15.5px;margin-top:12px}
.news-btn{width:139px;height:36px;line-height:36px;background:var(--navy);font-family:"Roboto Condensed",sans-serif;font-size:19px;text-align:center;margin-top:14px}
.address{display:flex;gap:12px}
.copyright{left:0;top:2516px;width:1200px;height:74px;background:var(--navy)}
.copyright p{position:absolute;left:82px;top:26px;font-size:14px;color:var(--white)}
.social{position:absolute;top:29px;width:46px;height:46px;border-radius:50%;border:2px solid var(--blue)}
</style>
</head>
<body>
<div class="abs topline"></div>
<header class="abs site-header">
  <div class="abs brand"><span class="brand-dot"></span>Quillbrookes</div>
  <nav class="abs main-nav">
    <a class="active" href="#">Home</a><a href="#">Founder</a><a href="#">Consultancy</a><a href="#">System</a><a href="#">Case Studies</a><a href="#">Contact</a>
  </nav>
</header>

<section class="abs hero">
  <svg width="1200" height="625" role="img" aria-label="Photo of business people in a meeting around an office table">
    <defs>
      <linearGradient id="heroPhoto" x1="0" y1="0" x2="1" y2="1">
        <stop offset="0" stop-color="#b9c3cc"/><stop offset=".5" stop-color="#d6dde3"/><stop offset="1" stop-color="#6e7f93"/>
      </linearGradient>
    </defs>
    <rect width="1200" height="625" fill="url(#heroPhoto)"/>
    <polygon points="0,0 515,0 400,625 0,625" fill="#2b2f36" opacity=".6"/>
  </svg>
  <h1 class="abs hero-title">Traditional and<br>non-traditional pools of<br>liquidity</h1>
  <a class="abs btn btn-contact" href="#">Contact Us</a>
</section>

<h2 class="abs welcome-title">WELCOME TO <span>QUILLBROOKES</span></h2>
<p class="abs welcome-text">Quillbrookes Consultancy Limited capitalizes on synergies arising from trade and investment linkages between countries and knowledge of traditional and non-traditional pools of liquidity to provide consultancy services to Emerging country banks, Corporates and SMEs.</p>
<a class="abs btn btn-more" href="#">Read More</a>

<section class="abs consultancy"></section>
<h2 class="abs section-title" style="top:1128px">CONSULTANCY</h2>
<p class="abs section-lead" style="top:1191px">QCL will work with you to understand your business and offer need based strategic and transactional advice which fits your corporate strategy.</p>

<article class="abs card card-dark">
  <div class="card-icon">
    <svg width="78" height="78" viewBox="0 0 78 78" aria-hidden="true">
      <circle cx="39" cy="39" r="26" fill="none" stroke="#1e2a44" stroke-width="6" stroke-dasharray="22 12"/>
      <circle cx="39" cy="12" r="8" fill="#1e2a44"/><circle cx="62" cy="52" r="8" fill="#1e2a44"/><circle cx="16" cy="52" r="8" fill="#1e2a44"/>
    </svg>
  </div>
  <h3>PLAIN VANILLA FINANCING SOLUTIONS</h3>
  <span class="rule"></span>
  <p>The Consultancy provides access to local/regional banks across Hong Kong, Singapore, Dubai , New York and London and helps corporate clients in diversifying their financial partners and adding new banks to their bank group.</p>
</article>

<article class="abs card card-blue">
  <div class="card-icon">
    <svg width="80" height="70" viewBox="0 0 80 70" aria-hidden="true" fill="#0b8ad6">
      <rect x="30" y="0" width="20" height="16" rx="2"/>
      <rect x="38" y="16" width="4" height="12"/><rect x="10" y="26" width="60" height="4"/>
      <rect x="10" y="26" width="4" height="14"/><rect x="38" y="26" width="4" height="14"/><rect x="66" y="26" width="4" height="14"/>
      <rect x="0" y="40" width="22" height="16" rx="2"/><rect x="29" y="40" width="22" height="16" rx="2"/><rect x="58" y="40" width="22" height="16" rx="2"/>
    </svg>
  </div>
  <h3>STRUCTURED FINANCING SOLUTIONS</h3>
  <span class="rule"></span>
  <p>The Consultancy provides end-to-end structured solutions on the Payables, Receivables or Inventory side for working capital requirements with off/part/on recourse balance sheet structures. We also specialize in providing credit enhancements ...</p>
</article>

<section class="abs case-study">
  <svg width="1200" height="470" role="img" aria-label="Photo of colleagues shaking hands in an office, dimmed with a navy tint">
    <defs>
      <linearGradient id="casePhoto" x1="0" y1="0" x2="1" y2="0">
        <stop offset="0" stop-color="#3b4660"/><stop offset=".5" stop-color="#56627a"/><stop offset="1" stop-color="#3e4a63"/>
      </linearGradient>
    </defs>
    <rect width="1200" height="470" fill="url(#casePhoto)"/>
  </svg>
</section>
<h2 class="abs case-title">CASE STUDY</h2>
<p class="abs case-lead">Some of the deals completed by QCL are summarised below to describe the range of activities undertaken with Corporates.</p>
<p class="abs case-facts"><b>Annual turnover of customer :</b> New Company<br><b>Annual group turnover:</b> Over USD 550.0 million<br><b>Facility Arranged :</b> USD 8.4 million</p>
<svg class="abs slide-arrow" style="left:45px" viewBox="0 0 62 62" aria-label="Previous"><circle cx="31" cy="31" r="29" fill="none" stroke="#fff" stroke-width="2"/><polyline points="35,17 23,31 35,45" fill="none" stroke="#fff" stroke-width="2"/></svg>
<svg class="abs slide-arrow" style="left:1090px" viewBox="0 0 62 62" aria-label="Next"><circle cx="31" cy="31" r="29" fill="none" stroke="#fff" stroke-width="2"/><polyline points="27,17 39,31 27,45" fill="none" stroke="#fff" stroke-width="2"/></svg>
<div class="abs case-banner">QUILLBROOKES &nbsp;– Export Credit Agency backed long term financing</div>

<footer class="abs site-footer"></footer>
<div class="abs footer-col" style="left:78px;width:220px;top:2262px">
  <div class="brand footer-brand"><span class="brand-dot"></span>Quillbrookes</div>
  <p style="margin-top:8px">Quillbrookes Consultancy Limited capitalizes on synergies arising from trade and investment linkages.</p>
</div>
<div class="abs footer-col" style="left:347px">
  <h4>Useful Links</h4>
  <ul><li>Home</li><li>Founder</li><li>Consultancy</li><li>System</li><li>Case study</li><li>Contact</li></ul>
</div>
<div class="abs footer-col" style="left:620px;width:250px">
  <h4>Newsletter</h4>
  <p>Lorem Ipsum is simply dummy text of the printing.</p>
  <div class="news-input">Enter Email Id</div>
  <div class="news-btn">SUBSCRIBE</div>
</div>
<div class="abs footer-col" style="left:893px;width:260px">
  <h4>Get In Touch</h4>
  <div class="address">
    <svg width="14" height="20" viewBox="0 0 14 20" aria-hidden="true" style="flex:none;margin-top:4px"><path d="M7 0a7 7 0 0 0-7 7c0 5 7 13 7 13s7-8 7-13a7 7 0 0 0-7-7z" fill="#fff"/><circle cx="7" cy="7" r="2.6" fill="#0b8ad6"/></svg>
    <p>Quillbrookes Consultancy Ltd<br>Unit 04, 9th Floor,<br>Harbourline Tower,<br>27 Marlow Quay Road, Kowloon,<br>Hong Kong</p>
  </div>
</div>

<div class="abs copyright">
  <p>© <b>Quillbrookes</b> - &nbsp;2016. All Rights Reserved</p>
  <span class="social" style="left:857px;border-color:#fff" aria-label="Social link"></span>
  <span class="social" style="left:934px" aria-label="Social link"></span>
  <span class="social" style="left:1003px" aria-label="Social link"></span>
  <span class="social" style="left:1075px" aria-label="Social link"></span>
</div>
</body>
</html>
```